Corvane Holdings , new business card design

investment firm with corporate clients . need double sided business card , vertical and horizontal options ,logo must be clear. prefer pantone colors only and sharp design. website also www.corvane.ae

Khalid Bin Tarrafi
Managing Director
Tel. +971 4 387 2940
Mobile +971 50 518 2403
khalid@corvane.ae
Q-Span Plaza, officw 18-B07, Warqa Gardens, Dubai

Contact Information for Business Card

Khalid Bin Tarrafi
Managing Director

Font styles to use
Serif

Colors

Designer to choose colors to be used in the design.

```html
<!DOCTYPE html>
<html lang="en">
<head>
<meta charset="utf-8">
<title>Corvane Holdings – Business Card</title>
<link rel="stylesheet" href="https://fonts.googleapis.com/css2?family=Jost:wght@400;600&display=swap">
<style>
  :root {
    --backdrop: #7a4a26;
    --card-light: #d9ae80;
    --card-mid: #c89461;
    --card-dark: #b47e4c;
    --ink: #141008;
    --rule: #2a1d10;
  }
  * { margin: 0; padding: 0; box-sizing: border-box; }
  html, body {
    width: 1200px; height: 900px; overflow: hidden;
    background: var(--backdrop);
    font-family: "Jost", "Century Gothic", sans-serif;
    color: var(--ink);
  }
  .stage { position: relative; width: 1200px; height: 900px; }
  .card {
    position: absolute;
    background: linear-gradient(160deg, var(--card-light) 0%, var(--card-mid) 55%, var(--card-dark) 100%);
    display: flex; flex-direction: column; align-items: center; justify-content: center;
    text-align: center;
  }
  .card--front { left: 330px; top: 90px; width: 555px; height: 343px; }
  .card--back  { left: 330px; top: 469px; width: 559px; height: 343px; }

  .holder-name { font-weight: 600; font-size: 17.5px; letter-spacing: 0.02em; line-height: 20px; }
  .holder-role { font-size: 16px; line-height: 20px; }
  .rule { width: 186px; height: 1px; background: var(--rule); margin: 10px 0 12px; }
  .contact-list { list-style: none; font-size: 15.5px; line-height: 20px; }
  .contact-list b { font-weight: 600; }
  .address { font-size: 15.5px; line-height: 20px; }

  .brand { display: flex; flex-direction: column; align-items: center; margin-top: 14px; }
  .brand-name {
    font-weight: 400; font-size: 46px; letter-spacing: 0.36em; margin-right: -0.36em;
    line-height: 50px;
  }
  .brand-sub {
    font-weight: 400; font-size: 14px; letter-spacing: 0.72em; margin-right: -0.72em;
    line-height: 18px; margin-top: 4px;
  }
</style>
</head>
<body>
<main class="stage">
  <section class="card card--front" aria-label="Card front">
    <h1 class="holder-name">KHALID BIN TARRAFI</h1>
    <p class="holder-role">Managing Director</p>
    <div class="rule"></div>
    <ul class="contact-list">
      <li><b>P:</b> +971 4 387 2940</li>
      <li><b>M:</b> +971 50 518 2403</li>
      <li><b>E:</b> khalid@corvane.ae</li>
      <li><b>W:</b> www.corvane.ae</li>
    </ul>
    <div class="rule"></div>
    <p class="address">Q-Span Plaza, officw 18-B07<br>Warqa Gardens, Dubai</p>
  </section>

  <section class="card card--back" aria-label="Card back">
    <div class="brand">
      <span class="brand-name">CORVANE</span>
      <span class="brand-sub">HOLDINGS</span>
    </div>
  </section>
</main>
</body>
</html>
```